Business card design Needed for new logo / Construction business, home extensions and new builds

We need a business card design using our new logo files which i will attach to this project :)

We are a small construction business specialising in home extensions, new builds and property development. We are very ambitious and would appreciate professional and elegant designs for our new business card.

Very serious about using the services on MakerQuarry and recently acquired our new logo from here :)

Please get involved, i will feedback when i can as i am very busy but can respond daily, thanks

Target Market(s)

People that want to build onto their houses, new building developments or adding too their existing property

Industry/Entity Type

Construction

Contact Information for Business Card

Renwick Tolliver Construction, Lionel Ashby (Managing Director), Tel 07822254961, email - info@renwick-tolliver, www.renwick-tolliver.co.uk

Colors

Designer to choose colors to be used in the design.

Requirements
Must have
• I like a deep grey on the back please. A lot of you have provided black from and back, try mixing things up a little. The black looks cool 😎 Thanks

```html
<!DOCTYPE html>
<html lang="en">
<head>
<meta charset="utf-8">
<title>Renwick Tolliver Construction – Business Card</title>
<link rel="stylesheet" href="https://fonts.googleapis.com/css2?family=Open+Sans:wght@400;600;700&display=swap">
<style>
  :root {
    --page: #2a2a2e;
    --card-front: #1d1d21;
    --card-back: #242428;
    --gold: #d9a12a;
    --gold-light: #f2c45a;
    --gold-dark: #a8741a;
    --silver: #d8d9dc;
    --silver-dark: #8e9096;
    --text-light: #ececee;
    --rule: #6f7075;
  }
  * { box-sizing: border-box; margin: 0; padding: 0; }
  html, body {
    width: 1200px; height: 780px; overflow: hidden;
    background: var(--page);
    font-family: "Open Sans", Arial, sans-serif;
  }
  .canvas { position: relative; width: 1200px; height: 780px; }
  .card {
    position: absolute; top: 230px;
    width: 560px; height: 320px;
    box-shadow: 0 10px 30px rgba(0,0,0,.45);
    overflow: hidden;
  }
  .card--front { left: 30px; background: var(--card-front); }
  .card--back  { left: 610px; background: var(--card-back); }

  .brand {
    position: absolute; text-align: center;
    color: var(--gold); font-weight: 600;
    text-transform: uppercase; letter-spacing: 2px; line-height: 1.35;
  }
  .card--front .brand { left: 30px; top: 90px; width: 240px; font-size: 15px; }
  .card--back .brand  { left: 0; top: 120px; width: 560px; font-size: 24px; letter-spacing: 4px; }

  .divider { position: absolute; left: 0; top: 0; width: 560px; height: 320px; }

  .contact { position: absolute; left: 318px; top: 100px; }
  .contact__name { font-size: 27px; font-weight: 700; line-height: 1.1; }
  .contact__name .first { color: var(--silver); }
  .contact__name .last  { color: var(--gold); }
  .contact__role { color: var(--text-light); font-size: 13px; margin-top: 3px; }
  .contact__list { list-style: none; margin-top: 18px; }
  .contact__item {
    display: flex; align-items: center; gap: 8px;
    color: var(--text-light); font-size: 12.5px; line-height: 22px;
  }
  .contact__icon { width: 12px; height: 12px; flex: none; }

  .address-band {
    position: absolute; left: 0; top: 278px; width: 480px; height: 26px;
    background: linear-gradient(180deg, var(--gold-light), var(--gold) 55%, var(--gold-dark));
    color: #fff; font-size: 12px; font-weight: 600;
    line-height: 26px; padding-left: 26px; white-space: nowrap;
  }
  .address-band__tip {
    position: absolute; left: 480px; top: 278px; width: 80px; height: 26px;
    background: linear-gradient(180deg, #f4f4f6, var(--silver) 50%, var(--silver-dark));
  }
  .band-brand {
    position: absolute; left: 420px; top: 256px; width: 120px; text-align: right;
    color: var(--gold); font-size: 9px; font-weight: 600;
    text-transform: uppercase; letter-spacing: 1px; white-space: nowrap;
  }
</style>
</head>
<body>
<main class="canvas">

  <section class="card card--front" aria-label="Business card front">
    <div class="brand">Renwick Tolliver<br>Construction</div>

    <svg class="divider" viewBox="0 0 560 320" aria-hidden="true">
      <line x1="300" y1="58" x2="258" y2="252" stroke="var(--rule)" stroke-width="1"/>
    </svg>

    <div class="contact">
      <div class="contact__name"><span class="first">Lionel</span> <span class="last">Ashby</span></div>
      <div class="contact__role">Managing Director</div>
      <ul class="contact__list">
        <li class="contact__item">
          <svg class="contact__icon" viewBox="0 0 24 24" aria-hidden="true"><path fill="var(--gold)" d="M6.6 10.8a15 15 0 0 0 6.6 6.6l2.2-2.2a1 1 0 0 1 1-.25 11.4 11.4 0 0 0 3.6.57 1 1 0 0 1 1 1V20a1 1 0 0 1-1 1A17 17 0 0 1 3 4a1 1 0 0 1 1-1h3.5a1 1 0 0 1 1 1c0 1.25.2 2.450.57 3.6a1 1 0 0 1-.25 1z"/></svg>
          07822 254 961
        </li>
        <li class="contact__item">
          <svg class="contact__icon" viewBox="0 0 24 24" aria-hidden="true"><rect x="2" y="5" width="20" height="14" rx="1.5" fill="var(--gold)"/><path d="M3 6l9 7 9-7" fill="none" stroke="#1d1d21" stroke-width="1.8"/></svg>
          info@renwick-tolliver.co.uk
        </li>
        <li class="contact__item">
          <svg class="contact__icon" viewBox="0 0 24 24" aria-hidden="true"><circle cx="12" cy="12" r="10" fill="var(--gold)"/><path d="M2 12h20M12 2c3 3 3 17 0 20M12 2c-3 3-3 17 0 20" fill="none" stroke="#1d1d21" stroke-width="1.5"/></svg>
          www.renwick-tolliver.co.uk
        </li>
      </ul>
    </div>

    <div class="address-band">Hollins Lane, Marrowfield Kestbury, KX7 4RN</div>
    <div class="address-band__tip"></div>
    <div class="band-brand">Renwick Tolliver</div>
  </section>

  <section class="card card--back" aria-label="Business card back">
    <div class="brand">Renwick Tolliver<br>Construction</div>
  </section>

</main>
</body>
</html>
```